jQuery Mobile CSS for web app

Task Outline:
Create jQuery Mobile themeroller compliant CSS and icons for a mobile web app.
Task Description:
Brindle Solutions are in the process of implementing a new, web based version of their Tessel operations platform.
The web based version of Tessel is built on top of the jQuery Mobile platform and we are looking for a designer to create a jQuery Mobile themeroller compliant CSS theme pack that we can plug into our application. The aim is to remove the standard jQuery Mobile look and feel and to introduce the Brindle branding throughout the new web app.
A number of screenshots are shown in the attached design spec (brindle_solutions.pdf) that show what the current (Windows Mobile 6.5) application looks like, alongside the development version of our new web app.
Deliverables:
• jQuery Mobile (v 1.4.2) themeroller compliant CSS which provides theming for all jQuery Mobile UI components.
• Example html showing how to use the CSS theme (especially where additional html/css classes are required).
• New set of status icons (as listed in attachment)
Inspiration:
See our website for current branding: www.brindle-solutions-demo.net

```html
<!DOCTYPE html>
<html lang="en">
<head>
<meta charset="utf-8">
<title>Brindle Tessel – Task List</title>
<link rel="stylesheet" href="https://fonts.googleapis.com/css2?family=Open+Sans:wght@400;600&display=swap">
<style>
  :root {
    --bg: #1b1b1b;
    --row-bg: #1c1c1c;
    --row-line: #2c2c2c;
    --header-top: #333333;
    --header-bottom: #1c1c1c;
    --divider: #3a3a3a;
    --text-main: #f2f2f2;
    --text-sub: #a9a9a9;
    --tick-top: #e3475b;
    --tick-bottom: #a8101f;
    --bar-top: #2b2b2b;
    --bar-bottom: #1a1a1a;
    --bar-active-top: #c9c9c9;
    --bar-active-bottom: #a9a9a9;
    --icon-grey: #8a8a8a;
  }
  * { box-sizing: border-box; margin: 0; padding: 0; }
  html, body {
    width: 830px; height: 1200px; overflow: hidden;
    background: var(--bg);
    font-family: "Open Sans", Arial, sans-serif;
  }
  .app { position: relative; width: 830px; height: 1200px; }

  .app-header {
    position: absolute; top: 0; left: 0; width: 830px; height: 122px;
    background: linear-gradient(var(--header-top), var(--header-bottom));
    border-bottom: 2px solid #111;
  }
  .brand-name {
    position: absolute; left: 38px; top: 22px;
    font-size: 52px; font-weight: 600; color: #ffffff; letter-spacing: -0.5px;
  }
  .header-divider {
    position: absolute; top: 22px; width: 1px; height: 72px; background: var(--divider);
  }
  .header-divider.left { left: 277px; }
  .header-divider.right { left: 729px; }
  .app-title {
    position: absolute; left: 315px; top: 47px;
    font-size: 19px; color: #ffffff; letter-spacing: 0.3px;
  }
  .menu-button { position: absolute; left: 763px; top: 44px; }

  .task-list { position: absolute; top: 122px; left: 0; width: 830px; height: 961px; overflow: hidden; list-style: none; }
  .task-item {
    position: relative; height: 226px; background: var(--row-bg);
    border-bottom: 3px solid var(--row-line);
  }
  .task-icon {
    position: absolute; left: 54px; top: 49px; width: 131px; height: 131px;
    border-radius: 16px;
    background: linear-gradient(var(--tick-top), var(--tick-bottom));
    box-shadow: 0 4px 8px rgba(0,0,0,0.6);
  }
  .task-icon svg { position: absolute; left: 22px; top: 24px; }
  .task-title {
    position: absolute; left: 241px; top: 64px;
    font-size: 33px; color: var(--text-main); white-space: nowrap;
  }
  .task-hint {
    position: absolute; left: 241px; top: 118px;
    font-size: 22px; color: var(--text-sub);
  }

  .nav-bar {
    position: absolute; left: 0; top: 1083px; width: 830px; height: 117px;
    display: flex; border-top: 2px solid #0e0e0e;
  }
  .nav-button {
    position: relative; width: 277px; height: 100%;
    background: linear-gradient(var(--bar-top), var(--bar-bottom));
    border-right: 2px solid #111;
    display: flex; align-items: center; justify-content: center;
  }
  .nav-button:last-child { border-right: none; flex: 1; }
  .nav-button.is-active { background: linear-gradient(var(--bar-active-top), var(--bar-active-bottom)); }
  .build-code {
    position: absolute; right: 29px; top: 49px;
    font-size: 16px; color: #ffffff;
  }
</style>
</head>
<body>
<div class="app">
  <header class="app-header">
    <div class="brand-name">Brindle</div>
    <div class="header-divider left"></div>
    <div class="app-title">BRINDLE TESSEL</div>
    <div class="header-divider right"></div>
    <svg class="menu-button" width="36" height="32" viewBox="0 0 36 32" aria-label="Menu">
      <rect x="0" y="0" width="36" height="4" fill="#fff"/>
      <rect x="0" y="13" width="36" height="4" fill="#fff"/>
      <rect x="0" y="26" width="36" height="4" fill="#fff"/>
    </svg>
  </header>

  <ul class="task-list">
    <li class="task-item">
      <span class="task-icon"><svg width="88" height="84" viewBox="0 0 88 84"><path d="M6 48 L18 38 L34 58 L78 6 L84 14 L36 76 Z" fill="#fff"/></svg></span>
      <span class="task-title">Crew</span>
      <span class="task-hint">Tap to view and edit the crew</span>
    </li>
    <li class="task-item">
      <span class="task-icon"><svg width="88" height="84" viewBox="0 0 88 84"><path d="M6 48 L18 38 L34 58 L78 6 L84 14 L36 76 Z" fill="#fff"/></svg></span>
      <span class="task-title">Materials / Subcontractor…</span>
      <span class="task-hint">Tap to view and edit the crew</span>
    </li>
    <li class="task-item">
      <span class="task-icon"><svg width="88" height="84" viewBox="0 0 88 84"><path d="M6 48 L18 38 L34 58 L78 6 L84 14 L36 76 Z" fill="#fff"/></svg></span>
      <span class="task-title">Crew</span>
      <span class="task-hint">Tap to view and edit the crew</span>
    </li>
    <li class="task-item">
      <span class="task-icon"><svg width="88" height="84" viewBox="0 0 88 84"><path d="M6 48 L18 38 L34 58 L78 6 L84 14 L36 76 Z" fill="#fff"/></svg></span>
      <span class="task-title">Materials / Subcontractor…</span>
      <span class="task-hint">Tap to view and edit the crew</span>
    </li>
    <li class="task-item"></li>
  </ul>

  <nav class="nav-bar">
    <div class="nav-button is-active">
      <svg width="72" height="46" viewBox="0 0 72 46" aria-label="Back">
        <path d="M20 4 L4 15 L20 26" fill="none" stroke="#000" stroke-width="5" stroke-linejoin="round"/>
        <path d="M6 15 H54 A14 14 0 0 1 54 43 H22" fill="none" stroke="#000" stroke-width="5"/>
      </svg>
    </div>
    <div class="nav-button">
      <svg width="78" height="40" viewBox="0 0 78 40" aria-label="Home">
        <path d="M3 37 V16 L39 3 L75 16 V37 Z" fill="none" stroke="var(--icon-grey)" stroke-width="4" stroke-linejoin="round"/>
      </svg>
    </div>
    <div class="nav-button">
      <svg width="72" height="46" viewBox="0 0 72 46" aria-label="Forward">
        <path d="M48 4 L66 15 L48 26 Z" fill="var(--icon-grey)"/>
        <path d="M50 15 H18 A14 14 0 0 0 18 43 H46" fill="none" stroke="var(--icon-grey)" stroke-width="6"/>
      </svg>
      <span class="build-code">C8</span>
    </div>
  </nav>
</div>
</body>
</html>
```